Meridale Bed Company Needs Business Card

Looking for a very nice looking business card. Creative but not extravagant. We sell beds and pillows across the U.S. and need something professional but catchy. I have attached the logo.

Name : Devin Holt
Title : President
Phone : (800) 471-2960
Email: sleep@quilmora.com
Website: www.quilmora.com

Can be single-sided or double-sided
horizontal or vertical

Can use Blues/Greys

Target Market(s)

Mass Market

Industry/Entity Type

Retail

Contact Information for Business Card

Name : Devin Holt
Title : President
Phone : (800) 471-2960
Email: sleep@quilmora.com
Website: www.quilmora.com

Requirements
Must have
• Clean, Modern, Smooth
• Can use Blues/Greys
• On the other side without the information - have something simple like www.quilmora.com or our logo
Nice to have
• Surprise me
Should not have
• Nothing crazy, nothing cluttered

```html
<!DOCTYPE html>
<html lang="en">
<head>
<meta charset="utf-8">
<title>Meridale Bed Company – Business Card</title>
<link href="https://fonts.googleapis.com/css2?family=Montserrat:wght@400;500;700&display=swap" rel="stylesheet">
<style>
  :root {
    --stage: #2a2a2a;
    --card-dark: #3b3b3b;
    --card-light: #ffffff;
    --brand-blue: #2aa3dc;
    --text-grey: #4a4a4a;
    --text-light: #e9e9e9;
    --rule-grey: #9a9a9a;
  }
  * { margin: 0; padding: 0; box-sizing: border-box; }
  html, body { width: 1200px; height: 900px; overflow: hidden; }
  body {
    background: var(--stage);
    position: relative;
    font-family: "Montserrat", Arial, sans-serif;
  }
  .card {
    position: absolute;
    width: 560px;
    height: 320px;
    border-radius: 22px;
    box-shadow: 0 12px 30px rgba(0,0,0,0.45);
  }
  .card-back {
    left: 60px; top: 110px;
    background: var(--card-dark);
  }
  .card-front {
    left: 580px; top: 470px;
    background: var(--card-light);
  }
  .brand-name {
    font-family: "Montserrat", Arial, sans-serif;
    font-weight: 500;
    color: var(--brand-blue);
    line-height: 1;
    position: absolute;
    white-space: nowrap;
  }
  .card-back .brand-name {
    font-size: 80px;
    left: 0; right: 0; top: 112px;
    text-align: center;
  }
  .back-url {
    position: absolute;
    left: 0; right: 0; bottom: 40px;
    text-align: center;
    font-size: 17px;
    color: var(--text-light);
    letter-spacing: 0.5px;
  }
  .back-url .url-accent { color: var(--brand-blue); }
  .card-front .brand-name {
    font-size: 46px;
    left: 40px; top: 138px;
  }
  .divider {
    position: absolute;
    left: 318px; top: 92px;
    width: 1px; height: 140px;
    background: linear-gradient(to bottom, transparent, var(--rule-grey) 25%, var(--rule-grey) 75%, transparent);
  }
  .contact {
    position: absolute;
    left: 340px; top: 100px;
  }
  .contact-name {
    font-weight: 700;
    font-size: 22px;
    color: var(--brand-blue);
    line-height: 1.1;
  }
  .contact-title {
    font-size: 13px;
    color: var(--text-grey);
    margin: 2px 0 14px 8px;
  }
  .contact-list { list-style: none; margin-left: 8px; }
  .contact-list li {
    display: flex; align-items: center; gap: 7px;
    font-size: 14px;
    color: var(--text-grey);
    line-height: 1.45;
  }
  .contact-list svg { width: 11px; height: 11px; flex: none; }
</style>
</head>
<body>
  <section class="card card-back" aria-label="Business card back">
    <div class="brand-name">quilmora</div>
    <div class="back-url">www.<span class="url-accent">quilmora</span>.com</div>
  </section>

  <section class="card card-front" aria-label="Business card front">
    <div class="brand-name">quilmora</div>
    <div class="divider"></div>
    <div class="contact">
      <div class="contact-name">Devin Holt</div>
      <div class="contact-title">President</div>
      <ul class="contact-list">
        <li>
          <svg viewBox="0 0 24 24" aria-hidden="true"><path fill="#2aa3dc" d="M6.6 10.8a15 15 0 0 0 6.6 6.6l2.2-2.2c.3-.3.7-.4 1-.2 1.1.4 2.3.6 3.6.6.6 0 1 .4 1 1V20c0 .6-.4 1-1 1A17 17 0 0 1 3 4c0-.6.4-1 1-1h3.5c.6 0 1 .4 1 1 0 1.3.2 2.5.6 3.6.1.3 0 .7-.2 1z"/></svg>
          (800) 471-2960
        </li>
        <li>
          <svg viewBox="0 0 24 24" aria-hidden="true"><rect x="2" y="5" width="20" height="14" rx="2" fill="none" stroke="#2aa3dc" stroke-width="2.4"/><path d="M3 6l9 7 9-7" fill="none" stroke="#2aa3dc" stroke-width="2.4"/></svg>
          sleep@quilmora.com
        </li>
        <li>
          <svg viewBox="0 0 24 24" aria-hidden="true"><circle cx="12" cy="12" r="10" fill="none" stroke="#2aa3dc" stroke-width="2.2"/><ellipse cx="12" cy="12" rx="4.5" ry="10" fill="none" stroke="#2aa3dc" stroke-width="2"/><path d="M2 12h20" stroke="#2aa3dc" stroke-width="2"/></svg>
          www.quilmora.com
        </li>
      </ul>
    </div>
  </section>
</body>
</html>
```